My company is throwing a party. The name is 80/20 (80% Calypso & 20% Whatever Remains)

I seek a flyer that shows this will be a very elegant, upscale event and at the same time high energy, great reggae music and dancing.

I need this flyer to be 650 pixels wide & any length, High resolution (1MB) for printing on a 4" x 6" flyer.

Target Market(s)

Fans of reggae music

Industry/Entity Type

Printing

Requirements
Must have
• Radiant Holdings Presents:
80/20
Upscale Reggae Soiree
80% Calypso - 20% Whatever Remains

Saturday May 4th, 10pm - 3am

The Lantern: 412 1/2 North Hollis Blvd, OKC

Dress to impress! We reserve the right to refuse entry

Free Entry: 1st 50 Ladies On VIP Guestlist - Discounted Early Bird Online Tickets - For Bottle Service Reservation: http://islandnight.ticketmarlo.com

More info? 405-555-0187

```html
<!DOCTYPE html>
<html lang="en">
<head>
<meta charset="utf-8">
<title>80/20 — Upscale Reggae Soiree</title>
<link rel="stylesheet" href="https://fonts.googleapis.com/css2?family=Bebas+Neue&family=Jost:wght@400;600;700&display=swap">
<style>
  :root {
    --ink: #000000;
    --paper: #ffffff;
    --hot-pink: #e8177f;
    --blush: #f3cde0;
    --ghost: #2b2427;
    --light-magenta: #ff4fa8;
    --light-orange: #ff8a3a;
    --light-violet: #7b2fbf;
    --light-blue: #2f5fd0;
  }
  * { box-sizing: border-box; margin: 0; padding: 0; }
  html, body { width: 800px; height: 1200px; overflow: hidden; background: var(--ink); }
  .flyer {
    position: relative;
    width: 800px;
    height: 1200px;
    overflow: hidden;
    background: var(--ink);
    color: var(--paper);
    font-family: "Jost", sans-serif;
  }
  .party-scene {
    position: absolute;
    left: 0; top: 0;
    width: 800px; height: 480px;
    background:
      linear-gradient(180deg, rgba(0,0,0,0) 45%, rgba(0,0,0,0.85) 85%, var(--ink) 100%),
      radial-gradient(ellipse 45% 55% at 50% 20%, #fff0f6 0%, var(--light-magenta) 35%, rgba(232,23,127,0) 75%),
      linear-gradient(90deg, var(--light-blue) 0%, var(--light-violet) 22%, var(--hot-pink) 50%, var(--light-orange) 85%, #c8402a 100%);
  }
  .title-ghost {
    position: absolute;
    left: 0; top: 420px;
    width: 800px; height: 520px;
  }
  .host {
    position: absolute;
    top: 388px; left: 0; width: 800px;
    display: flex; justify-content: center; align-items: center; gap: 12px;
    font-size: 30px;
    color: var(--paper);
  }
  .host-mark {
    width: 40px; height: 40px;
    border: 2px solid var(--paper);
    border-radius: 50%;
  }
  .host-name { font-weight: 600; }
  .host-presents { font-weight: 400; font-size: 26px; }
  .title {
    position: absolute;
    left: 0; top: 480px;
    width: 800px; height: 250px;
  }
  .info {
    position: absolute;
    left: 0; top: 762px; width: 800px;
    text-align: center;
  }
  .subtitle { font-weight: 700; font-size: 35px; line-height: 1; }
  .split { margin-top: 14px; font-size: 24px; line-height: 30px; }
  .split strong, .accent { color: var(--hot-pink); font-weight: 700; }
  .when { margin-top: 10px; font-size: 24px; line-height: 30px; }
  .when strong { font-weight: 700; }
  .dress { margin-top: 22px; font-size: 24px; line-height: 30px; }
  .dress strong { color: var(--blush); font-weight: 700; }
  .offers { margin-top: 20px; font-size: 24px; line-height: 40px; }
  .offers strong { font-weight: 700; }
  .offers sup { font-size: 13px; }
  .offers .link { font-style: italic; }
  .contact {
    position: absolute;
    left: 0; bottom: 28px; width: 800px;
    display: flex; justify-content: space-between;
    padding: 0 36px 0 36px;
    font-size: 20px;
  }
  .contact-item { display: flex; align-items: center; gap: 12px; white-space: nowrap; }
  .contact-item strong { font-weight: 600; }
</style>
</head>
<body>
<div class="flyer">
  <div class="party-scene" role="img" aria-label="Party crowd in silhouette with raised hands under colourful disco lights, framed by palm trees"></div>

  <svg class="title-ghost" viewBox="0 0 800 520" aria-hidden="true">
    <text x="-30" y="500" font-family="Bebas Neue, sans-serif" font-size="560" fill="var(--ghost)" textLength="860" lengthAdjust="spacingAndGlyphs">80/20</text>
  </svg>

  <div class="host"><span class="host-mark"></span><span class="host-name">Radiant Holdings</span><span class="host-presents">Presents:</span></div>

  <svg class="title" viewBox="0 0 800 250" role="img" aria-label="80/20">
    <text x="200" y="245" font-family="Bebas Neue, sans-serif" font-size="280" fill="var(--hot-pink)" textLength="400" lengthAdjust="spacingAndGlyphs">80/20</text>
  </svg>

  <div class="info">
    <p class="subtitle">Upscale Reggae Soiree</p>
    <p class="split"><strong>80%</strong> Calypso - <strong>20%</strong> Whatever Remains</p>
    <p class="when"><strong>Saturday May 4th</strong>, 10pm - 3am</p>
    <p class="dress"><strong>Dress to impress!</strong> We reserve the right to refuse entry</p>
    <p class="offers">
      <strong>Free Entry:</strong> 1<sup>st</sup> 50 Ladies On VIP Guestlist <span class="accent">&#9830;</span> Discounted<br>
      Early Bird Online Tickets <span class="accent">&#9830;</span> For Bottle Service Reservation:<br>
      <span class="link">http://islandnight.ticketmarlo.com</span>
    </p>
  </div>

  <div class="contact">
    <div class="contact-item">
      <svg width="24" height="34" viewBox="0 0 24 34" aria-hidden="true">
        <path d="M12 0C5.4 0 0 5.3 0 11.9 0 20.5 12 34 12 34s12-13.5 12-22.1C24 5.3 18.6 0 12 0zm0 17a5.2 5.2 0 1 1 0-10.4A5.2 5.2 0 0 1 12 17z" fill="var(--paper)"/>
      </svg>
      <span><strong>The Lantern:</strong> 412 1/2 North Hollis Blvd, OKC</span>
    </div>
    <div class="contact-item">
      <svg width="30" height="34" viewBox="0 0 30 34" aria-hidden="true">
        <path d="M7 1l5 8-4 3c2 6 5 10 10 13l3-4 8 5-3 6C15 33 1 17 2 4z" fill="var(--paper)"/>
      </svg>
      <span>405-555-0187</span>
    </div>
  </div>
</div>
</body>
</html>
```